Dental office stationary (letterhead, envelopes), business cards, presentation folders

Nothing too dental outside of the logo. I will need all stationary, presentation folders, business cards. Would prefer to stay in the colors of the logo

Gordon Patel, DDS
Bright Haven Dental Implant Center
555-318-2790
info@brighthavendental.example
4817 NW Maple Crest Rd Unit B
Stuart, FL 00000

Also need appointment date and time
And cancellation policy
I want it to say “kindly ask for
A 48hr cancellation policy to avoid incurring a cancellation fee”

Industry/Entity Type

Dental

Colors
0054AA
0677BA
7BADD7
CADEEF
E8F1F8

Requirements
Must have
• Name of your office, name of doctor, address, phone number
Should not have
• Too much tooth/dental. Only the tooth in logo

```html
<!DOCTYPE html>
<html lang="en">
<head>
<meta charset="UTF-8">
<title>Bright Haven Dental Implant Center – Business Card</title>
<link href="https://fonts.googleapis.com/css2?family=Roboto:wght@400;500;700&display=swap" rel="stylesheet">
<style>
  :root {
    --page-bg: #e6eaee;
    --card-bg: #212121;
    --teal: #14b9a0;
    --sky: #19c0ef;
    --deep-blue: #0e64bf;
    --name-blue: #1cb4ea;
    --text-light: #f2f2f2;
    --divider: #d8d8d8;
  }
  * { margin: 0; padding: 0; box-sizing: border-box; }
  html, body {
    width: 1200px; height: 900px; overflow: hidden;
    background: var(--page-bg);
    font-family: "Roboto", Arial, sans-serif;
  }
  .sheet {
    width: 1200px; height: 900px;
    display: flex; flex-direction: column; align-items: center; justify-content: center;
    gap: 30px;
  }
  .card {
    position: relative;
    width: 700px; height: 400px;
    background: var(--card-bg);
    overflow: hidden;
    box-shadow: 0 10px 30px rgba(0,0,0,0.25);
  }
  .card-art { position: absolute; inset: 0; }

  /* Front */
  .brand-name {
    position: absolute; left: 44px; top: 44px;
    color: var(--sky);
    font-weight: 500;
    line-height: 1.1;
  }
  .brand-name .brand-main { display: block; font-size: 40px; letter-spacing: 2px; text-transform: uppercase; }
  .brand-name .brand-sub { display: block; font-size: 15px; letter-spacing: 5px; text-transform: uppercase; margin-top: 6px; }

  .divider {
    position: absolute; left: 330px; top: 148px;
    width: 1.5px; height: 126px;
    background: var(--divider);
  }
  .contact {
    position: absolute; left: 350px; top: 148px;
    color: var(--text-light);
  }
  .contact-name { color: var(--name-blue); font-weight: 700; font-size: 24px; line-height: 28px; }
  .contact-office { font-size: 16px; line-height: 20px; margin-top: 2px; }
  .contact-list { list-style: none; margin-top: 10px; }
  .contact-list li {
    display: flex; align-items: center; gap: 8px;
    font-size: 15.5px; line-height: 24px;
  }
  .contact-list svg { width: 14px; height: 14px; flex: none; }

  .address {
    position: absolute; left: 36px; top: 340px;
    color: #ffffff; font-size: 16px; line-height: 20px;
  }

  /* Back */
  .card-back { display: flex; align-items: center; justify-content: center; }
  .back-name { color: var(--sky); font-weight: 500; text-align: center; line-height: 1.1; }
  .back-name .brand-main { display: block; font-size: 56px; letter-spacing: 3px; text-transform: uppercase; }
  .back-name .brand-sub { display: block; font-size: 20px; letter-spacing: 7px; text-transform: uppercase; margin-top: 10px; }
</style>
</head>
<body>
<main class="sheet">

  <section class="card card-front">
    <svg class="card-art" viewBox="0 0 700 400" width="700" height="400" aria-hidden="true">
      <defs>
        <linearGradient id="swoosh" x1="0" y1="0" x2="1" y2="1">
          <stop offset="0" stop-color="#19c0ef"/>
          <stop offset="0.6" stop-color="#0e7fcf"/>
          <stop offset="1" stop-color="#0a5bb3"/>
        </linearGradient>
      </defs>
      <path d="M0,262 Q430,262 560,400 L0,400 Z" fill="#14b9a0"/>
      <path d="M10,248 Q460,248 595,400 L580,400 Q445,262 10,248 Z" fill="url(#swoosh)"/>
    </svg>

    <div class="brand-name">
      <span class="brand-main">Bright Haven</span>
      <span class="brand-sub">Dental Implant Center</span>
    </div>

    <div class="divider"></div>

    <div class="contact">
      <div class="contact-name">Gordon Patel, DDS</div>
      <div class="contact-office">Bright Haven Dental Implant Center</div>
      <ul class="contact-list">
        <li>
          <svg viewBox="0 0 16 16"><path fill="#14b9a0" d="M3.6 1.5l2.3 2.6-1.3 1.8c.9 2 2.5 3.6 4.5 4.5l1.8-1.3 2.6 2.3-1.4 2.1C6.9 15.2.8 9.1 1.5 3z"/></svg>
          555-318-2790
        </li>
        <li>
          <svg viewBox="0 0 16 16"><rect x="1" y="3" width="14" height="10" rx="1" fill="#14b9a0"/><path d="M1.5 3.8L8 9l6.5-5.2" stroke="#212121" stroke-width="1.4" fill="none"/></svg>
          info@brighthavendental.example
        </li>
        <li>
          <svg viewBox="0 0 16 16"><circle cx="8" cy="8" r="7" fill="#14b9a0"/><path d="M1 8h14M8 1c-3 3-3 11 0 14M8 1c3 3 3 11 0 14" stroke="#212121" stroke-width="1.1" fill="none"/></svg>
          www.brighthavendental.example
        </li>
      </ul>
    </div>

    <div class="address">4817 NW Maple Crest Rd Unit B, Harbor Point, ST 00000</div>
  </section>

  <section class="card card-back">
    <div class="back-name">
      <span class="brand-main">Bright Haven</span>
      <span class="brand-sub">Dental Implant Center</span>
    </div>
  </section>

</main>
</body>
</html>
```